GlassHaven Artbook for Okanagan Region, British Columbia

Creating an art book: GlassHaven, for the Okanagan Wine Region in British Columbia, Canada. Would like smart, modern, clean and linear...cool, sexy urban, not ugly boring suburban... I need a cover that appeals to the wino in all of us! Title: GlassHaven -Marla Dovicki
Updates
Thank you all kindly for your efforts. I have added some files so that you can get a sense of my aesthetic...it's never easy trying to figure it out, is it? I will hopefully have dimensions of book soon...cheers, Marla
would anyone please design a giant wine bottle with the wine label that looks like a label but says glasshaven...just curious to see if it works as a design or not...thank you.
Target Market(s)
Designing this wine art book of quotes to wineries in Okanagan BC. Buyer is wine lover and tourist ready to spend his vacation bucks on this wonderful book!
Look and feel

```html
<!DOCTYPE html>
<html lang="en">
<head>
<meta charset="utf-8">
<title>GlassHaven – Cover</title>
<link rel="stylesheet" href="https://fonts.googleapis.com/css2?family=Bebas+Neue&family=Oswald:wght@400&display=swap">
<style>
  :root {
    --frame: #dfe3b6;
    --teal: #4fbfae;
    --teal-shadow: #3a9f90;
    --bottle-red: #ef625c;
    --bottle-dark: #4a3a30;
    --bottle-mint: #6edcbd;
    --title-yellow: #e2d338;
    --author-ink: #3e3029;
  }
  html, body {
    margin: 0;
    padding: 0;
    width: 938px;
    height: 1200px;
    overflow: hidden;
    background: var(--frame);
  }
  .cover {
    position: relative;
    width: 938px;
    height: 1200px;
    background: var(--frame);
  }
  .cover__panel {
    position: absolute;
    left: 37px;
    top: 37px;
    width: 864px;
    height: 1126px;
    background: var(--teal);
  }
  .cover__shadow {
    position: absolute;
    left: 200px;
    top: 935px;
    width: 540px;
    height: 50px;
    border-radius: 50%;
    background: var(--teal-shadow);
    opacity: 0.5;
    filter: blur(14px);
  }
  .cover__artwork {
    position: absolute;
    left: 263px;
    top: 152px;
    width: 421px;
    height: 816px;
    background: linear-gradient(90deg,
      var(--bottle-red) 0%, var(--bottle-red) 24%,
      var(--bottle-dark) 36%, var(--bottle-dark) 64%,
      var(--bottle-mint) 76%, var(--bottle-mint) 100%);
  }
  .cover__title {
    position: absolute;
    left: 0;
    top: 0;
    width: 938px;
    height: 1200px;
    overflow: visible;
  }
  .cover__title text {
    font-family: "Bebas Neue", "Oswald", sans-serif;
    font-size: 200px;
    fill: var(--title-yellow);
  }
  .cover__author {
    position: absolute;
    left: 0;
    top: 1010px;
    width: 938px;
    margin: 0;
    text-align: center;
    font-family: "Oswald", sans-serif;
    font-weight: 400;
    font-size: 48px;
    line-height: 60px;
    letter-spacing: 4px;
    color: var(--author-ink);
  }
</style>
</head>
<body>
<main class="cover">
  <div class="cover__panel"></div>
  <div class="cover__shadow"></div>
  <div class="cover__artwork" role="img" aria-label="Three overlapping wine bottle silhouettes in coral red, dark brown and mint green"></div>
  <svg class="cover__title" viewBox="0 0 938 1200" xmlns="http://www.w3.org/2000/svg">
    <text transform="translate(404,258) rotate(90)" textLength="640" lengthAdjust="spacingAndGlyphs">GLASSHAVEN</text>
  </svg>
  <p class="cover__author">MARLA DOVICKI</p>
</main>
</body>
</html>
```